Dovetree baby skincare

design business cards (double sided) and complimentary note (single sided)

Industry/Entity Type

Business

Colors

Designer to choose colors to be used in the design.

```html
<!DOCTYPE html>
<html lang="en">
<head>
<meta charset="utf-8">
<title>Dovetree baby skincare – business card</title>
<link rel="stylesheet" href="https://fonts.googleapis.com/css2?family=Open+Sans:wght@400;700&display=swap">
<style>
  :root {
    --backdrop: #e9e9e7;
    --card: #fdfdfc;
    --gold: #c8a444;
    --peach-strong: #f1c9ad;
    --peach-soft: #f8e3d4;
    --ink: #1c1c1c;
    --shadow: rgba(0, 0, 0, 0.12);
  }
  html, body {
    margin: 0;
    padding: 0;
    width: 1200px;
    height: 800px;
    overflow: hidden;
    background: var(--backdrop);
    font-family: "Open Sans", Arial, sans-serif;
  }
  .canvas {
    position: relative;
    width: 1200px;
    height: 800px;
  }
  .card {
    position: absolute;
    top: 240px;
    width: 540px;
    height: 320px;
    background: var(--card);
    overflow: hidden;
    box-shadow: 0 6px 18px var(--shadow);
  }
  .card--front { left: 40px; }
  .card--back { left: 620px; }

  .swash {
    position: absolute;
    inset: 0;
    width: 100%;
    height: 100%;
  }
  .wordmark {
    position: absolute;
    margin: 0;
    color: var(--gold);
    font-weight: 700;
    letter-spacing: -1px;
    line-height: 1;
  }
  .card--front .wordmark {
    left: 0;
    right: 0;
    top: 128px;
    text-align: center;
    font-size: 66px;
  }
  .card--back .wordmark {
    left: 200px;
    top: 70px;
    font-size: 50px;
  }
  .contact {
    position: absolute;
    left: 34px;
    bottom: 30px;
    margin: 0;
    color: var(--ink);
    font-size: 15px;
    line-height: 1.35;
  }
  .contact__name {
    display: block;
    font-size: 20px;
    margin-bottom: 2px;
  }
</style>
</head>
<body>
<main class="canvas">

  <section class="card card--front" aria-label="Business card front">
    <svg class="swash" viewBox="0 0 540 320" role="img" aria-label="Soft peach watercolour brush stroke">
      <defs>
        <linearGradient id="swash-front" x1="0" y1="0" x2="0" y2="1">
          <stop offset="0" stop-color="var(--peach-soft)"/>
          <stop offset="1" stop-color="var(--peach-strong)"/>
        </linearGradient>
      </defs>
      <path d="M300 -10 L400 -10 L330 300 L240 290 Z" fill="url(#swash-front)" opacity="0.85"/>
    </svg>
    <h1 class="wordmark">dovetree</h1>
  </section>

  <section class="card card--back" aria-label="Business card back">
    <svg class="swash" viewBox="0 0 540 320" role="img" aria-label="Soft peach watercolour brush stroke">
      <defs>
        <linearGradient id="swash-back" x1="0" y1="0" x2="0" y2="1">
          <stop offset="0" stop-color="var(--peach-soft)"/>
          <stop offset="1" stop-color="var(--peach-strong)"/>
        </linearGradient>
      </defs>
      <path d="M400 -10 L500 -10 L470 170 L385 160 Z" fill="url(#swash-back)" opacity="0.85"/>
    </svg>
    <h2 class="wordmark">dovetree</h2>
    <p class="contact">
      <span class="contact__name">Maren Holt-Ellis</span>
      CEO<br>
      9012 4478<br>
      0400 123 987<br>
      maren@dovetreeskincare.com<br>
      www.dovetreeskincare.com
    </p>
  </section>

</main>
</body>
</html>
```